Business cards in digital learning for freelancer

Hello, I need a business cards in french. I work in the Digital learning industries as freeelancer; I'm an expert in digital learning. I work in France. My customer are in the health industry, pharmaceutical industry, and training organization. I've got a logo. I offer three services: consulting, Design, and Training. In the consulting, I offers coaching to choose your digital learning tools and the digital learning strategy. For the Design, I product differents level of elearning like rapid-learning, elearning, micro-learning, video-learning. And for the training service, I've create training about pedagogy, digital learning management project, Digital learning design.
I join my Logo create in this platform. My universe is gamified. I like the life, and I'm very social. I want a card like I'm I. I love Art (painting), Europeen comics. I use in my visual support "permanent maker" font and caracters. I would like cards: elegant, modern, Top class. If you need any information, you can ask me.
thanks for ideas

Target Market(s)

in health industries and training organization for Training manager, instructor, human resources director

Contact Information for Business Card

Phone number : 06 71 38 95 14 , mail: bastiengolmier@quelmoto.fr, web: bastiengolmier.fr , Carrivo

Font styles to use
Sans Serif

Requirements
Must have
• Use my logo and write my 3 services (consulting, training, design)

```html
<!DOCTYPE html>
<html lang="fr">
<head>
<meta charset="utf-8">
<title>Golmier Digital Learning – Cartes de visite</title>
<link rel="stylesheet" href="https://fonts.googleapis.com/css2?family=Cinzel:wght@400&family=Roboto:wght@400;700&display=swap">
<style>
  :root {
    --orange: #f37321;
    --white: #ffffff;
    --grey-text: #4a4a4a;
    --grey-mark: #6f6f6f;
    --grey-line: #8a8a8a;
    --backdrop: #a3a3a3;
  }
  * { margin: 0; padding: 0; box-sizing: border-box; }
  html, body {
    width: 1200px; height: 1200px; overflow: hidden;
    background: var(--backdrop);
    font-family: "Roboto", Arial, sans-serif;
  }
  .stage { position: relative; width: 1200px; height: 1200px; }
  .card {
    position: absolute; top: 303px; height: 594px; border-radius: 12px; overflow: hidden;
  }
  .card--front { left: 201px; width: 369px; background: var(--orange); color: var(--white); }
  .card--back { left: 599px; width: 364px; background: var(--white); color: var(--grey-text); }

  .centered { position: absolute; left: 0; right: 0; text-align: center; white-space: nowrap; }

  .brand-name { font-family: "Roboto", Arial, sans-serif; font-weight: 700; font-size: 34px; letter-spacing: 4px; line-height: 34px; height: 34px; }
  .card--back .brand-name { color: var(--orange); }

  .tagline { display: flex; align-items: center; justify-content: center; gap: 8px;
    font-family: "Cinzel", Georgia, serif; font-size: 13px; letter-spacing: 1px; line-height: 14px; height: 14px; }
  .tagline .rule { display: block; width: 54px; height: 1px; background: currentColor; }
  .card--back .tagline { color: var(--grey-mark); }
  .card--back .tagline .rule { background: var(--grey-text); }

  .services { font-size: 15.5px; letter-spacing: 0.2px; line-height: 16px; display: flex; justify-content: center; align-items: center; gap: 8px; }
  .services .dot { width: 8px; height: 8px; border-radius: 50%; background: currentColor; display: inline-block; }
  .card--back .services .dot { background: var(--orange); }

  .person-name { font-family: "Cinzel", Georgia, serif; color: var(--orange); font-size: 24px; letter-spacing: 0.5px; line-height: 24px; }
  .person-role { font-size: 17px; line-height: 18px; }

  .divider-row { display: flex; align-items: center; justify-content: center; gap: 6px; }
  .divider-row .rule { width: 52px; height: 1px; background: var(--grey-line); }
  .divider-row .rule--wide { width: 76px; }
  .icon-box { width: 25px; height: 25px; background: var(--orange); border-radius: 3px; display: flex; align-items: center; justify-content: center; }
  .contact { font-size: 17px; line-height: 21px; }

  .social { display: flex; align-items: center; justify-content: center; gap: 8px; }
  .social .badge { width: 26px; height: 26px; border-radius: 50%; background: var(--orange); }
  .social .label { font-size: 15px; color: var(--orange); }
</style>
</head>
<body>
<main class="stage">

  <section class="card card--front" aria-label="Recto">
    <div class="centered brand-name" style="top:467px;">GOLMIER</div>
    <div class="centered tagline" style="top:506px;"><span class="rule"></span>DIGITAL LEARNING<span class="rule"></span></div>
    <div class="centered services" style="top:540px;">CONSULTING <span class="dot"></span> TRAINING <span class="dot"></span> DESIGN</div>
  </section>

  <section class="card card--back" aria-label="Verso">
    <div class="centered brand-name" style="top:200px;">GOLMIER</div>
    <div class="centered tagline" style="top:239px;"><span class="rule"></span>DIGITAL LEARNING<span class="rule"></span></div>
    <div class="centered services" style="top:272px;">CONSULTING <span class="dot"></span> TRAINING <span class="dot"></span> DESIGN</div>

    <div class="centered person-name" style="top:370px;">JULIEN MARCEAU</div>
    <div class="centered person-role" style="top:397px;">Managing Director</div>

    <div class="centered divider-row" style="top:430px;">
      <span class="rule"></span>
      <span class="icon-box"><svg width="15" height="13" viewBox="0 0 15 13"><path d="M1 4 Q7.5 -1 14 4 L12 6 L10 4.5 L5 4.5 L3 6 Z" fill="#fff"/><rect x="3" y="6" width="9" height="6" rx="1" fill="#fff"/></svg></span>
      <span class="icon-box"><svg width="15" height="11" viewBox="0 0 15 11"><rect x="0.75" y="0.75" width="13.5" height="9.5" fill="none" stroke="#fff" stroke-width="1.5"/><path d="M1 1 L7.5 6 L14 1" fill="none" stroke="#fff" stroke-width="1.5"/></svg></span>
      <span class="icon-box"><svg width="15" height="15" viewBox="0 0 15 15"><circle cx="7.5" cy="7.5" r="6.5" fill="none" stroke="#fff" stroke-width="1.5"/><path d="M1 7.5 H14 M7.5 1 Q4 7.5 7.5 14 M7.5 1 Q11 7.5 7.5 14" fill="none" stroke="#fff" stroke-width="1.2"/></svg></span>
      <span class="rule"></span>
    </div>

    <div class="centered contact" style="top:466px;">06 71 38 95 14<br>bastiengolmier@quelmoto.fr<br>www.bastiengolmier.fr</div>

    <div class="centered divider-row" style="top:542px;">
      <span class="rule rule--wide"></span>
      <span class="social"><span class="badge"></span><span class="label">Carrivo</span></span>
      <span class="rule rule--wide"></span>
    </div>
  </section>

</main>
</body>
</html>
```